Maple Gable Business Card

Colors can be blue, grey and white as you see in the attached logo. Needs to have a spot for name, title, phone, email, address, and website. There also needs to be a spot for an agent's picture.

Contact Information for Business Card

See project description.

Colors

Designer to choose colors to be used in the design.

```html
<!DOCTYPE html>
<html lang="en">
<head>
<meta charset="utf-8">
<title>Maple Gable Business Card</title>
<link href="https://fonts.googleapis.com/css2?family=Roboto:wght@400;700&display=swap" rel="stylesheet">
<style>
  :root {
    --stage: #2e2622;
    --card-grey: #58595b;
    --brand-blue: #2a78c2;
    --ink-grey: #555a60;
    --paper: #ffffff;
    --photo-light: #e9ecef;
    --photo-dark: #1d1f24;
  }
  * { box-sizing: border-box; margin: 0; padding: 0; }
  html, body { width: 1200px; height: 716px; overflow: hidden; }
  body {
    background: var(--stage);
    font-family: "Roboto", Arial, sans-serif;
    position: relative;
  }
  .card {
    position: absolute;
    top: 210px;
    width: 520px;
    height: 297px;
    overflow: hidden;
    box-shadow: 0 10px 28px rgba(0,0,0,.45);
  }
  .card--back { left: 50px; background: var(--card-grey); }
  .card--front { left: 630px; background: var(--paper); }

  .card__edge {
    position: absolute;
    left: 0; bottom: 0;
    height: 8px;
    background: var(--brand-blue);
  }
  .card--back .card__edge { width: 100%; }
  .card--front .card__edge { width: 100%; }

  .brand {
    font-family: "Roboto", Arial, sans-serif;
    font-weight: 700;
    color: var(--brand-blue);
    text-transform: uppercase;
    letter-spacing: 1px;
    display: flex;
    align-items: center;
    gap: 10px;
  }
  .brand__dot {
    width: 14px; height: 14px;
    background: var(--brand-blue);
  }
  .card--back .brand {
    position: absolute;
    left: 0; right: 0; top: 124px;
    justify-content: center;
    font-size: 36px;
  }
  .card--front .brand {
    position: absolute;
    left: 40px; top: 30px;
    font-size: 24px;
  }

  .agent {
    position: absolute;
    left: 40px; top: 82px;
    color: var(--ink-grey);
  }
  .agent__name {
    color: var(--brand-blue);
    font-weight: 700;
    font-size: 22px;
    line-height: 1.1;
  }
  .agent__title { font-size: 15px; margin-top: 2px; }
  .agent__address { font-size: 14px; margin-top: 10px; line-height: 1.35; }
  .contact { list-style: none; margin-top: 10px; font-size: 14px; line-height: 1.55; }
  .contact li { display: flex; align-items: center; gap: 8px; }
  .contact svg { width: 13px; height: 13px; flex: none; }
  .contact__accent { color: var(--brand-blue); }

  .agent-photo {
    position: absolute;
    right: 30px; bottom: 8px;
    width: 210px; height: 220px;
    background: linear-gradient(180deg, var(--photo-light) 0%, #8a8f97 45%, var(--photo-dark) 100%);
    border-radius: 90px 90px 0 0;
  }
</style>
</head>
<body>
  <section class="card card--back" aria-label="Card back">
    <div class="brand"><span class="brand__dot"></span>Maple Gable</div>
    <div class="card__edge"></div>
  </section>

  <section class="card card--front" aria-label="Card front">
    <div class="brand"><span class="brand__dot"></span>Maple Gable</div>

    <div class="agent">
      <h1 class="agent__name">Daniel Harper</h1>
      <p class="agent__title">Manager</p>
      <p class="agent__address">Your address, city<br>state, ZIP 0000</p>
      <ul class="contact">
        <li>
          <svg viewBox="0 0 24 24" fill="#2a78c2" aria-hidden="true"><path d="M6.6 10.8a15.1 15.1 0 0 0 6.6 6.6l2.2-2.2c.3-.3.7-.4 1-.2 1.1.4 2.3.6 3.6.6.6 0 1 .4 1 1V20c0 .6-.4 1-1 1A17 17 0 0 1 3 4c0-.6.4-1 1-1h3.5c.6 0 1 .4 1 1 0 1.3.2 2.5.6 3.6.1.3 0 .7-.2 1z"/></svg>
          555-014-2100
        </li>
        <li>
          <svg viewBox="0 0 24 24" fill="#2a78c2" aria-hidden="true"><path d="M2 5h20v14H2z" fill="none" stroke="#2a78c2" stroke-width="2"/><path d="M2 5l10 8 10-8" fill="none" stroke="#2a78c2" stroke-width="2"/></svg>
          youremail@mailhub.com
        </li>
        <li>
          <svg viewBox="0 0 24 24" aria-hidden="true"><circle cx="12" cy="12" r="10" fill="none" stroke="#2a78c2" stroke-width="2"/><path d="M2 12h20M12 2c3 3 3 17 0 20M12 2c-3 3-3 17 0 20" fill="none" stroke="#2a78c2" stroke-width="1.6"/></svg>
          <span>www.<span class="contact__accent">yourwebsite</span>.com</span>
        </li>
      </ul>
    </div>

    <div class="agent-photo" role="img" aria-label="Portrait photo of the agent in a dark suit and blue tie"></div>
    <div class="card__edge"></div>
  </section>
</body>
</html>
```